A New and modern Business Card for Tarwick Trade Solutions Ltd

New and modern Logo and Business Card Attached is the current logo/business card designCurrently the business is called "Tarwick & Co." or TTS Ltd for short. This is subject to change.This business specialises in Telecoms and Energy. We work with the major networks (QV, K7, etc) and also offer Energy Products saving clients money off their energy bills.These are business to business services.The current design incorporates a Pheonix, indicating rebirth, starting something new.We would like to maintain the Phoenix element but a newer modern style.We love colours in the logo 3 max.The aim of this is to be ultra slick and modern. I envisage Tarwick & Co. on one side of the card with long descriptions on the other side.Side 1:TTS Ltd/Logo?Side 2:TTS Ltd/Logo/Graphic?Brogan & Co.Name:Address:Phone:Email:The design is mostly flexible but must incorporate a Phoenix.For example "Tarwick & Co." with a block phoenix behind the text...up to you.

Industry/Entity Type

Telecommunications

Contact Information for Business Card

Tarwick & Co.
Address:
Name:
Phone:
Email:

Logo Text

Tarwick & Co.

Colors
33a6d7
0792cd
acd037
9bcb3c
f78f20
fece3e

Requirements
Must have
• Phoenix
• 3/4 colours max
• Blue representing Technology (wireless)
• Green for Eco Energy
• Orange for Phoenix
• White business card background
Should not have
• phoenix must not all be red/ orange fire, we are a technology service company and the phoenix colours must represent this. Fire is not representative of our company.

```html
<!DOCTYPE html>
<html lang="en">
<head>
<meta charset="utf-8">
<title>Tarwick Trade Solutions Ltd – Business Card</title>
<link rel="stylesheet" href="https://fonts.googleapis.com/css2?family=Marcellus&family=Lato:wght@400&display=swap">
<style>
  :root {
    --stage: #5c5c5c;
    --white: #ffffff;
    --tech-blue: #0792cd;
    --sky-blue: #33a6d7;
    --eco-green: #9bcb3c;
    --phoenix-orange: #f78f20;
    --ink-blue: #0a6690;
    --card-shadow: rgba(0, 0, 0, 0.35);
  }
  * { box-sizing: border-box; margin: 0; padding: 0; }
  html, body {
    width: 1200px;
    height: 802px;
    overflow: hidden;
    background: var(--stage);
  }
  .stage { position: relative; width: 1200px; height: 802px; }
  .card {
    position: absolute;
    top: 274px;
    width: 443px;
    height: 264px;
    overflow: hidden;
    background: var(--white);
    box-shadow: 2px 4px 8px var(--card-shadow);
  }
  .card--front { left: 136px; }
  .card--back { left: 624px; }

  .front-art { position: absolute; inset: 0; }

  .contact {
    position: absolute;
    left: 24px;
    top: 133px;
    color: var(--ink-blue);
    font-family: "Lato", sans-serif;
  }
  .contact__name {
    font-family: "Marcellus", serif;
    font-size: 17px;
    letter-spacing: 0.5px;
    text-transform: uppercase;
    line-height: 18px;
  }
  .contact__role { font-size: 13px; line-height: 15px; }
  .contact__line {
    display: flex;
    align-items: center;
    gap: 4px;
    font-size: 13px;
    line-height: 16px;
    margin-left: -2px;
  }
  .contact__line:first-of-type { margin-top: 9px; }
  .contact__line svg { width: 11px; height: 11px; flex: none; }
  .contact__address { font-size: 13px; line-height: 16px; margin-top: 5px; }

  .brand {
    position: absolute;
    left: 0;
    right: 0;
    top: 62px;
    display: flex;
    flex-direction: column;
    align-items: center;
  }
  .brand__dot {
    width: 58px;
    height: 58px;
    border-radius: 50%;
    background: var(--phoenix-orange);
    margin-bottom: 38px;
  }
  .brand__name {
    font-family: "Marcellus", serif;
    font-size: 37px;
    line-height: 34px;
    letter-spacing: 0.5px;
    text-transform: uppercase;
    color: var(--tech-blue);
  }
  .brand__tagline {
    font-family: "Lato", sans-serif;
    font-size: 10.5px;
    line-height: 13px;
    letter-spacing: 0.6px;
    text-transform: uppercase;
    color: var(--eco-green);
    margin-top: 3px;
  }
</style>
</head>
<body>
<main class="stage">
  <section class="card card--front">
    <svg class="front-art" viewBox="0 0 443 264" width="443" height="264">
      <defs>
        <linearGradient id="sweepFill" x1="0" y1="0" x2="1" y2="1">
          <stop offset="0" stop-color="#33a6d7"/>
          <stop offset="1" stop-color="#0792cd"/>
        </linearGradient>
        <linearGradient id="phoenixFill" x1="0" y1="0" x2="0" y2="1">
          <stop offset="0" stop-color="#fece3e" stop-opacity="0.9"/>
          <stop offset="1" stop-color="#f78f20"/>
        </linearGradient>
      </defs>
      <path class="front-art__sweep" d="M158 0 H443 V264 H395 C330 240 255 170 212 100 C190 62 170 30 158 0 Z" fill="url(#sweepFill)"/>
      <path class="front-art__sweep-green" d="M245 150 C280 205 330 240 395 264 H330 C290 235 262 200 245 150 Z" fill="var(--eco-green)"/>
      <path role="img" aria-label="Stylised phoenix illustration in orange, blue and green" d="M360 70 C400 50 443 60 443 60 V264 H395 C360 230 340 170 360 70 Z" fill="url(#phoenixFill)"/>
    </svg>
    <div class="contact">
      <p class="contact__name">Daniel Hartley</p>
      <p class="contact__role">Managing Director</p>
      <p class="contact__line">
        <svg viewBox="0 0 12 12" aria-hidden="true"><path d="M1 4 C1 2 3 1 6 1 C9 1 11 2 11 4 L9 5 L8 3.5 H4 L3 5 Z M3 6 H9 L10 11 H2 Z" fill="#0a6690"/></svg>
        021-480 735 612
      </p>
      <p class="contact__line">
        <svg viewBox="0 0 12 12" aria-hidden="true"><rect x="1" y="2.5" width="10" height="7" fill="#0a6690"/><path d="M1 2.5 L6 6.5 L11 2.5" fill="none" stroke="#fff" stroke-width="1"/></svg>
        hello@tarwickco.com
      </p>
      <p class="contact__address">17 Harlow Street,<br>30918, Northfield</p>
    </div>
  </section>

  <section class="card card--back">
    <div class="brand">
      <span class="brand__dot" aria-hidden="true"></span>
      <p class="brand__name">Tarwick</p>
      <p class="brand__tagline">Trade Solutions Limited</p>
    </div>
  </section>
</main>
</body>
</html>
```